Informational Site for Advanced Chemistry R&D

The company develops oxidation chemistry for air, water, fuel pollution controls. The site has been prototyped at www.velquaresearch.example. Take a look. Now, the task is to design it for eye-catching beauty with use of color, on-page scroll-driven color transition and parallax effects. Should capture the themes: high technology, wow it's beautiful, modern, uncluttered, clean urban environment.

Target Market(s)

China Environmentally Conscious Government and Industry,

Industry/Entity Type

It Company

Number of Pages Required

3 page

Font styles to use
Sans Serif

Requirements
Must have
• Parallax effects, desktop compatible, Rich, Modern, Simple, Graphic
Nice to have
• Mobile Phone Compatible
Should not have
• Flash, or anything that is slow to load or requires high bandwidth

```html
<!DOCTYPE html>
<html lang="en">
<head>
<meta charset="utf-8">
<title>Velqua Science — Advanced Oxidation</title>
<link href="https://fonts.googleapis.com/css2?family=Raleway:wght@400;500;600&family=Open+Sans:wght@400;600&display=swap" rel="stylesheet">
<style>
:root{
  --brand:#1b7fc4;
  --brand-dark:#0f5f9e;
  --ink:#222a30;
  --muted:#8a9098;
  --light:#f4f6f8;
  --water:#1d8fd6;
  --air:#6ab43e;
  --fuel:#f39a14;
  --tile-green:#5ea53a;
  --tile-orange:#f6a01a;
  --tile-blue:#1f9ad6;
  --tile-navy:#1a6aa8;
  --contact:#1f78c1;
  --contact-deep:#16609e;
  --white:#ffffff;
}
*{box-sizing:border-box;margin:0;padding:0}
html,body{width:1200px;height:2812px;overflow:hidden}
body{font-family:"Open Sans",Arial,sans-serif;color:var(--ink);background:var(--white);position:relative}
.headline{font-family:"Raleway",Arial,sans-serif}
section,header{position:relative;width:1200px;overflow:hidden}

/* Hero */
.hero{height:585px}
.hero-art{position:absolute;inset:0;background:
  radial-gradient(ellipse 420px 210px at 600px 470px,#6fb842 0%,#8cc55c 40%,rgba(180,215,150,0) 75%),
  linear-gradient(180deg,#cfe6f5 0%,#e9f4fb 45%,#d6e9f4 70%,#a9c9de 100%)}
.nav-bar{position:absolute;left:0;top:0;width:1200px;height:130px}
.brand{position:absolute;left:178px;top:42px;display:flex;align-items:center;gap:12px;font-family:"Raleway",sans-serif;font-weight:600;font-size:34px;color:var(--brand)}
.brand-dot{width:40px;height:40px;border-radius:50%;background:var(--brand)}
.nav{position:absolute;top:56px;left:0;list-style:none;font-family:"Raleway",sans-serif;font-size:15px;font-weight:500;color:var(--brand-dark)}
.nav li{position:absolute;white-space:nowrap}
.nav .active::after{content:"";position:absolute;left:0;right:0;top:30px;height:3px;background:var(--brand)}
.hero-title{position:absolute;top:168px;width:100%;text-align:center;font-size:50px;font-weight:500;color:var(--brand)}
.hero-sub{position:absolute;top:226px;width:100%;text-align:center;font-size:27px;font-weight:500;color:var(--brand-dark)}
.slider-dots{position:absolute;top:549px;left:560px;display:flex;gap:6px}
.slider-dots span{width:17px;height:17px;border-radius:50%;background:var(--white)}
.slider-dots .on{background:#e8d46a}

/* Intro */
.intro{height:443px;background:var(--white);text-align:center}
.intro-title{position:absolute;top:50px;width:100%;font-size:33px;font-weight:400;color:var(--brand)}
.intro-lead{position:absolute;top:92px;width:100%;font-size:15px;color:#444}
.intro-body{position:absolute;top:130px;left:250px;width:700px;font-size:11px;line-height:18px;color:var(--muted)}
.pillar-line{position:absolute;top:250px;left:338px;width:530px;height:1px;background:#dfe3e6}
.pillar{position:absolute;top:196px;width:220px;margin-left:-110px}
.pillar-ring{width:108px;height:108px;margin:0 auto;border-radius:50%;border:3px solid #e6e9ec;background:var(--white);display:flex;align-items:center;justify-content:center}
.pillar-core{width:92px;height:92px;border-radius:50%;display:flex;align-items:center;justify-content:center}
.pillar h3{margin-top:14px;font-family:"Raleway",sans-serif;font-size:15px;font-weight:600;letter-spacing:.5px;color:#333}
.pillar p{margin-top:6px;font-size:10.5px;line-height:17px;color:var(--muted)}

/* Technology */
.technology{height:393px;background:var(--white);border-top:1px solid #eceff1}
.tech-copy{position:absolute;left:182px;top:86px;width:400px}
.tech-copy h2{font-size:32px;font-weight:400;color:#111;margin-bottom:14px}
.tech-copy p{font-size:10.5px;line-height:18px;color:#555}
.ticks{list-style:none;margin:12px 0 18px}
.ticks li{display:flex;align-items:center;gap:8px;font-size:10.5px;color:#444;height:25px}
.tick{width:14px;height:14px;border-radius:50%;background:#1ea6c6;display:flex;align-items:center;justify-content:center}
.tech-art{position:absolute;left:600px;top:0;width:600px;height:393px;background:
  radial-gradient(circle 160px at 330px 220px,#eaf3fa 0%,rgba(234,243,250,0) 100%),
  linear-gradient(160deg,#b9d3e6 0%,#8fb4d3 50%,#5f8fbc 100%)}

/* Solutions */
.solutions{height:570px}
.tile{position:absolute;width:600px;height:285px;color:var(--white);text-align:center}
.tile-art{position:absolute;inset:0}
.tile-body{position:absolute;left:0;right:0;top:58px}
.tile-icon{height:74px;display:flex;align-items:center;justify-content:center}
.tile h3{font-family:"Raleway",sans-serif;font-weight:400;font-size:23px;margin-top:14px}
.tile p{font-size:10.5px;line-height:17px;width:420px;margin:8px auto 0;opacity:.92}
.read-more{display:inline-block;margin-top:22px;border:1px solid var(--white);font-size:8.5px;letter-spacing:.5px;padding:4px 12px}
.tile.fuel{left:0;top:0}
.tile.fuel .tile-art{background:linear-gradient(135deg,#4f9a30,#72b148 60%,#5fa23a)}
.tile.voc{left:600px;top:0}
.tile.voc .tile-art{background:linear-gradient(135deg,#f7b02c,#f49410 60%,#f8a824)}
.tile.flue{left:0;top:285px}
.tile.flue .tile-art{background:linear-gradient(135deg,#2aa6dd,#1a8cc9 60%,#2b9ed6)}
.tile.wastewater{left:600px;top:285px}
.tile.wastewater .tile-art{background:linear-gradient(135deg,#1e78b8,#15609c 60%,#1c6cab)}
.solution-badge{position:absolute;left:546px;top:231px;width:108px;height:108px;border-radius:50%;background:var(--white);border:6px solid rgba(255,255,255,.55);background-clip:padding-box;display:flex;align-items:center;justify-content:center;text-align:center;font-family:"Raleway",sans-serif;font-size:14px;line-height:18px;color:#333;box-shadow:0 0 0 1px #e0e4e8}

/* Partners */
.partners{height:394px;background:var(--white);text-align:center}
.partners h2{position:absolute;top:62px;width:100%;font-size:24px;font-weight:400;color:var(--brand)}
.partners h2::after{content:"";position:absolute;left:570px;top:42px;width:60px;height:2px;background:var(--brand)}
.partner{position:absolute;top:140px;width:200px;margin-left:-100px}
.partner-mark{height:110px;display:flex;align-items:center;justify-content:center}
.partner-name{font-family:"Raleway",sans-serif;font-weight:600;font-size:17px;color:var(--brand)}
.partner-badge{width:96px;height:96px;border-radius:50%}
.partner p{margin-top:14px;font-size:11px;line-height:18px;color:#a2a7ad;letter-spacing:.3px}

/* Contact */
.contact{height:427px;background:linear-gradient(180deg,var(--contact),var(--contact-deep));color:var(--white)}
.contact h2{position:absolute;top:44px;width:100%;text-align:center;font-size:27px;font-weight:400}
.contact h2::after{content:"";position:absolute;left:556px;top:46px;width:88px;height:2px;background:var(--white)}
.contact-form{position:absolute;left:182px;top:120px;width:337px}
.field{display:block;width:337px;height:31px;background:var(--white);border:none;font-family:"Open Sans",sans-serif;font-size:10px;color:#999;padding:0 14px;margin-bottom:7px;line-height:31px}
.field.message{height:77px;line-height:20px;padding-top:6px}
.send{display:inline-block;margin-top:20px;background:#0b3b63;color:var(--white);font-size:11px;font-weight:600;padding:7px 20px;letter-spacing:.5px}
.contact-info{position:absolute;left:611px;top:118px;font-size:13px;line-height:26px}
.contact-line{display:flex;align-items:center;gap:10px}
.socials{display:flex;gap:6px;margin-top:14px}
.socials span{width:28px;height:28px;border-radius:50%;border:1.5px solid var(--white)}
.footer-rule{position:absolute;left:0;right:0;top:371px;height:1px;background:rgba(255,255,255,.25)}
.copyright{position:absolute;left:182px;top:392px;font-size:10.5px;color:rgba(255,255,255,.75)}
</style>
</head>
<body>

<header class="hero">
  <div class="hero-art" role="img" aria-label="Green globe with wind turbines and a clean city skyline floating among bright clouds"></div>
  <div class="nav-bar">
    <div class="brand"><span class="brand-dot"></span>Velqua Science</div>
    <ul class="nav">
      <li class="active" style="left:550px">HOME</li>
      <li style="left:647px">TECHNOLOGY</li>
      <li style="left:802px">PRODUCTS</li>
      <li style="left:936px">CONTACT</li>
    </ul>
  </div>
  <h1 class="hero-title headline">Advanced Oxidation</h1>
  <p class="hero-sub headline">Science for Environmental Pollution Management</p>
  <div class="slider-dots"><span class="on"></span><span></span><span></span><span></span></div>
</header>

<section class="intro">
  <h2 class="intro-title headline">NEW IDEAS FOR A CLEANER WORLD</h2>
  <p class="intro-lead">Environmental pollution control solutions employing nature's most reactive Free Radical</p>
  <p class="intro-body">Our research teams turn the hydroxyl radical into practical tools for cleaner skies, rivers and fuels. Each process is designed to run at low temperature and pressure, scale from pilot to plant, and leave only harmless products behind for cities across the region.</p>
  <div class="pillar-line"></div>
  <div class="pillar" style="left:338px">
    <div class="pillar-ring"><div class="pillar-core" style="background:var(--water)">
      <svg width="34" height="44" viewBox="0 0 34 44"><path d="M17 2C11 13 3 21 3 29a14 14 0 0 0 28 0C31 21 23 13 17 2z" fill="#fff"/><path d="M10 29a7 7 0 0 0 5 7" stroke="#1d8fd6" stroke-width="2.5" fill="none" stroke-linecap="round"/></svg>
    </div></div>
    <h3>WATER</h3>
    <p>Oxidation breaks down dissolved organic pollutants</p>
  </div>
  <div class="pillar" style="left:600px">
    <div class="pillar-ring"><div class="pillar-core" style="background:var(--air)">
      <svg width="48" height="48" viewBox="0 0 48 48" fill="#fff"><circle cx="24" cy="24" r="4"/><ellipse cx="24" cy="11" rx="7" ry="10"/><ellipse cx="24" cy="37" rx="7" ry="10"/><ellipse cx="11" cy="24" rx="10" ry="7"/><ellipse cx="37" cy="24" rx="10" ry="7"/><circle cx="24" cy="24" r="3" fill="#6ab43e"/></svg>
    </div></div>
    <h3>AIR</h3>
    <p>Radical chemistry scrubs harmful gases from air</p>
  </div>
  <div class="pillar" style="left:868px">
    <div class="pillar-ring"><div class="pillar-core" style="background:var(--fuel)">
      <svg width="36" height="46" viewBox="0 0 36 46"><path d="M18 2c2 10 14 15 14 28a14 14 0 0 1-28 0c0-8 5-12 7-17 2 5 4 7 6 8 2-6 1-13 1-19z" fill="#fff"/><path d="M18 24c1 5 7 7 7 12a7 7 0 0 1-14 0c0-4 4-6 7-12z" fill="#f39a14"/></svg>
    </div></div>
    <h3>FUEL</h3>
    <p>Cleaner fuels through low temperature desulfurization</p>
  </div>
</section>

<section class="technology">
  <div class="tech-copy">
    <h2 class="headline">ADVANCED OXIDATION</h2>
    <p>Advanced Oxidation refers to a variety of techniques employing the Hydroxyl Radical, an energetic, highly reactive cousin of the water molecule:</p>
    <ul class="ticks">
      <li><span class="tick"><svg width="8" height="8" viewBox="0 0 8 8"><path d="M1 4l2 2 4-4" stroke="#fff" stroke-width="1.5" fill="none"/></svg></span>To add oxygen to inorganic molecules</li>
      <li><span class="tick"><svg width="8" height="8" viewBox="0 0 8 8"><path d="M1 4l2 2 4-4" stroke="#fff" stroke-width="1.5" fill="none"/></svg></span>To remove hydrogen from organic molecules</li>
    </ul>
    <p>These transformations convert important industrial contaminants into reactive forms that can be captured or that disintegrate into harmless end products.</p>
  </div>
  <div class="tech-art" role="img" aria-label="Glossy silver molecular model on a soft blue background"></div>
</section>

<section class="solutions">
  <article class="tile fuel">
    <div class="tile-art" role="img" aria-label="Green-tinted photo of a refinery with tanks and pipework"></div>
    <div class="tile-body">
      <div class="tile-icon"><svg width="60" height="72" viewBox="0 0 60 72" fill="#fff"><rect x="6" y="10" width="48" height="60" rx="3"/><rect x="2" y="4" width="56" height="8" rx="2"/><rect x="2" y="28" width="56" height="5"/><path d="M30 38c4 6 8 9 8 14a8 8 0 0 1-16 0c0-5 4-8 8-14z" fill="#5ea53a"/></svg></div>
      <h3>Fuel Oil Desulfurization</h3>
      <p>Our proprietary low temperature and pressure advanced oxidation catalytic process reliably removes sulfur from diesel transportation</p>
      <span class="read-more">READ MORE</span>
    </div>
  </article>
  <article class="tile voc">
    <div class="tile-art" role="img" aria-label="Orange-tinted photo of a worker beside chemical barrels"></div>
    <div class="tile-body">
      <div class="tile-icon"><svg width="66" height="72" viewBox="0 0 66 72" fill="#fff"><rect x="8" y="2" width="32" height="30" rx="4"/><rect x="2" y="36" width="30" height="34" rx="4"/><rect x="36" y="36" width="28" height="34" rx="4"/><rect x="8" y="14" width="32" height="4" fill="#f6a01a"/><rect x="2" y="50" width="62" height="4" fill="#f6a01a"/></svg></div>
      <h3>Volatile Organic Compunds (VOC)</h3>
      <p>Alkanes, alkenes, halogenated hydrocarbons, aromatic hydrocarbons, esters, aldehydes, polycyclic aromatic hydrocarbons.</p>
      <span class="read-more">READ MORE</span>
    </div>
  </article>
  <article class="tile flue">
    <div class="tile-art" role="img" aria-label="Blue-tinted photo of an industrial plant with smokestacks"></div>
    <div class="tile-body">
      <div class="tile-icon"><svg width="70" height="72" viewBox="0 0 70 72" fill="#fff"><circle cx="46" cy="10" r="7"/><circle cx="56" cy="6" r="6"/><circle cx="36" cy="16" r="5"/><rect x="10" y="22" width="8" height="20"/><rect x="2" y="40" width="64" height="30"/><g fill="#1f9ad6"><rect x="10" y="50" width="10" height="6"/><rect x="26" y="50" width="10" height="6"/><rect x="42" y="50" width="10" height="6"/><rect x="10" y="60" width="10" height="6"/><rect x="26" y="60" width="10" height="6"/><rect x="42" y="60" width="10" height="6"/></g></svg></div>
      <h3>Flue Gas Scrubbing</h3>
      <p>Desulfurization and denitrification using our proprietary flue gas advanced oxidation catalytic process (FGAOC). Sulfur and nitrogen</p>
      <span class="read-more">READ MORE</span>
    </div>
  </article>
  <article class="tile wastewater">
    <div class="tile-art" role="img" aria-label="Blue-tinted photo of a wastewater treatment plant with large pipes"></div>
    <div class="tile-body">
      <div class="tile-icon"><svg width="64" height="72" viewBox="0 0 64 72" fill="none" stroke="#fff" stroke-width="4" stroke-linecap="round"><path d="M32 4c6 10 12 15 12 23a12 12 0 0 1-24 0c0-8 6-13 12-23z" fill="#fff" stroke="none"/><path d="M4 48c7-6 11 6 18 0s11 6 18 0 11 6 18 0"/><path d="M4 58c7-6 11 6 18 0s11 6 18 0 11 6 18 0"/><path d="M4 68c7-6 11 6 18 0s11 6 18 0 11 6 18 0"/></svg></div>
      <h3>Wastewater Treatment</h3>
      <p>Photoelectrocatalysed (PEC) anodic oxidation removes soluble organics. Novel anode design using our proprietary nano-carbon</p>
      <span class="read-more">READ MORE</span>
    </div>
  </article>
  <div class="solution-badge">OUR<br>SOLUTION</div>
</section>

<section class="partners">
  <h2 class="headline">OUR PARTNERS</h2>
  <div class="partner" style="left:346px">
    <div class="partner-mark"><span class="partner-name">Norvane Systems</span></div>
    <p>OUR SALES PARTNER<br>IN CHINA</p>
  </div>
  <div class="partner" style="left:510px">
    <div class="partner-mark"><span class="partner-name">Brightel Build</span></div>
    <p>OUR CONSTRUCTION<br>PARTNER IN CHINA</p>
  </div>
  <div class="partner" style="left:712px">
    <div class="partner-mark"><span class="partner-badge" style="background:#1f4f8f"></span></div>
    <p>OUR TECHNOLOGY<br>PARTNER IN CHINA</p>
  </div>
  <div class="partner" style="left:872px">
    <div class="partner-mark"><span class="partner-badge" style="background:#b9202c"></span></div>
    <p>OUR TECHNOLOGY<br>PARTNER IN CHINA</p>
  </div>
</section>

<section class="contact">
  <h2 class="headline">CONTACT US</h2>
  <form class="contact-form">
    <div class="field">Name</div>
    <div class="field">Email address</div>
    <div class="field message">Message</div>
    <span class="send">SEND</span>
  </form>
  <div class="contact-info">
    <div>Velqua Science Corporation</div>
    <div>Fernbrook, U.S.A.</div>
    <div class="contact-line" style="margin-top:8px">
      <svg width="14" height="14" viewBox="0 0 14 14"><path d="M3 1l3 3-1.5 2a8 8 0 0 0 3.5 3.5L10 8l3 3-2 2C6 13 1 8 1 3z" fill="#fff"/></svg>
      info@velquaresearch.example</div>
    <div class="contact-line">
      <svg width="14" height="12" viewBox="0 0 14 12"><rect x="0.5" y="0.5" width="13" height="11" fill="#fff"/><path d="M1 1l6 5 6-5" stroke="#1f78c1" stroke-width="1.2" fill="none"/></svg>
      +1 555 014 2290</div>
    <div class="socials"><span></span><span></span><span></span><span></span></div>
  </div>
  <div class="footer-rule"></div>
  <p class="copyright">© 2016 Company Name &nbsp;All right reserved &nbsp;Term of Use</p>
</section>

</body>
</html>
```